Tarvex Consulting

Hi,
I have my own network consulting business (just me)
and need to get a logo and business card design together,

Based in New Zealand,

Gareth Holloway
Unified Communications and Network Architect

/design engineer,
and would like this to be the basis for personal branding and company identity

• I have the basis for a optional logo - needs color -

```html
<!DOCTYPE html>
<html lang="en">
<head>
<meta charset="utf-8">
<title>Tarvex Consulting – Business Card</title>
<link href="https://fonts.googleapis.com/css2?family=Marcellus&family=Open+Sans:wght@400;600&display=swap" rel="stylesheet">
<style>
  :root {
    --backdrop: #1d1d1e;
    --card-white: #fbfbfc;
    --ink: #2b2b2b;
    --name-blue: #2a78b6;
    --icon-blue: #2f6fb0;
    --mark-violet: #5a4fc0;
    --deco-lilac: #c9bfe3;
    --deco-aqua: #b7e3ee;
    --back-glow: #43b9d8;
    --back-mid: #3c86c4;
    --back-edge: #3b3a9e;
    --white: #ffffff;
  }
  * { margin: 0; padding: 0; box-sizing: border-box; }
  html, body { width: 1200px; height: 895px; overflow: hidden; }
  body { background: var(--backdrop); position: relative; font-family: "Open Sans", Arial, sans-serif; }

  .card {
    position: absolute; top: 240px; width: 525px; height: 300px;
    border-radius: 22px; overflow: hidden;
    box-shadow: 0 2px 8px rgba(0,0,0,.5);
  }
  .card--front { left: 75px; background: var(--card-white); }
  .card--back {
    left: 608px;
    background: radial-gradient(ellipse 300px 230px at 150px 160px, var(--back-glow) 0%, var(--back-mid) 50%, var(--back-edge) 100%);
  }

  .brand-dot {
    position: absolute; left: 100px; top: 34px; width: 46px; height: 46px;
    border-radius: 50%; background: var(--mark-violet);
  }
  .brand-name {
    position: absolute; left: 20px; top: 112px;
    font-family: "Marcellus", Georgia, serif; font-size: 19px; color: var(--ink);
    text-transform: uppercase; letter-spacing: .2px; white-space: nowrap;
  }
  .brand-tagline {
    position: absolute; left: 20px; top: 137px;
    font-size: 8.5px; color: var(--ink); white-space: nowrap;
  }

  .person { position: absolute; left: 307px; top: 144px; }
  .person__name { font-size: 18px; font-weight: 600; color: var(--name-blue); line-height: 22px; }
  .person__role { font-size: 14px; color: var(--ink); line-height: 20px; }

  .address { position: absolute; left: 28px; top: 185px; font-size: 13px; color: var(--ink); }
  .contacts { position: absolute; left: 27px; top: 209px; list-style: none; }
  .contacts li { display: flex; align-items: center; height: 19px; font-size: 13px; color: var(--ink); }
  .contacts svg { width: 13px; height: 11px; margin-right: 7px; fill: var(--icon-blue); }

  .front-accent {
    position: absolute; left: 408px; top: 172px; width: 150px; height: 150px; border-radius: 50%;
    background: linear-gradient(90deg, var(--deco-lilac), var(--deco-aqua));
  }

  .back-accent {
    position: absolute; left: 80px; top: 95px; width: 130px; height: 130px; border-radius: 50%;
    background: rgba(255,255,255,.45);
  }
  .back-name {
    position: absolute; right: 25px; top: 233px;
    font-family: "Marcellus", Georgia, serif; font-size: 27px; color: var(--white);
    text-transform: uppercase; white-space: nowrap;
  }
  .back-tagline {
    position: absolute; right: 23px; top: 269px;
    font-size: 13px; color: var(--white); white-space: nowrap;
  }
</style>
</head>
<body>

<section class="card card--front" aria-label="Business card front">
  <span class="brand-dot" aria-hidden="true"></span>
  <p class="brand-name">Tarvex Consulting</p>
  <p class="brand-tagline">Unified Communications and Network Architect</p>

  <span class="front-accent" aria-hidden="true"></span>

  <div class="person">
    <p class="person__name">Gareth Holloway</p>
    <p class="person__role">Design Engineer</p>
  </div>

  <p class="address">Wellington 6011 New Zealand</p>
  <ul class="contacts">
    <li><svg viewBox="0 0 13 11" aria-hidden="true"><path d="M1 4c0-2 3-3 5.5-3S12 2 12 4l-2.5 1-1-1.5h-4l-1 1.5zM3 6h7l1 4H2z"/></svg>04 555 0192</li>
    <li><svg viewBox="0 0 13 11" aria-hidden="true"><rect x="1" y="7" width="2" height="4"/><rect x="4.5" y="5" width="2" height="6"/><rect x="8" y="2" width="2" height="9"/><rect x="11" y="0" width="2" height="11"/></svg>04 555 0192</li>
    <li><svg viewBox="0 0 13 11" aria-hidden="true"><path d="M1 1.5h11v8H1zM2 2.5v.3l4.5 3.2L11 2.8v-.3zm0 1.5v4.5h9V4L6.5 7z" fill-rule="evenodd"/></svg>gareth@tarvexconsulting.com</li>
    <li><svg viewBox="0 0 13 11" aria-hidden="true"><circle cx="6.5" cy="5.5" r="5"/><path d="M1.5 5.5h10M6.5 .5v10" stroke="#fff" stroke-width=".8"/></svg>www.tarvexconsulting.com</li>
  </ul>
</section>

<section class="card card--back" aria-label="Business card back">
  <span class="back-accent" aria-hidden="true"></span>
  <p class="back-name">Tarvex Consulting</p>
  <p class="back-tagline">Unified Communications and Network Architect</p>
</section>

</body>
</html>
```